WordPress Site That Reviews Footwear

We need a wordpress web design for an affiliate site called PaceKite. We review and do roundups on footwear products. The final design should be clean and mobile friendly. The site should be built with Gutenberg page builder. We like the design of https://lunavessel.com/.
Updates

Need extra days to review

Target Market(s)

USA

Industry/Entity Type

Footwear

Logo Text

PaceKite

Number of Pages Required

4 page

Font styles to use
Serif
Sans Serif

Requirements
Must have
• Wordpress site
Blog post
Page
Categories
Homepage

```html
<!DOCTYPE html>
<html lang="en">
<head>
<meta charset="utf-8">
<title>PaceKite — Blogs</title>
<link href="https://fonts.googleapis.com/css2?family=Jost:wght@300;400;500;600&display=swap" rel="stylesheet">
<style>
:root{
  --brand:#1d56b6;
  --hero:#0c2f72;
  --ink:#111111;
  --muted:#555b66;
  --line:#d5d8de;
  --paper:#ffffff;
  --footer:#0b0b0b;
  --footer-text:#e8e8e8;
}
*{margin:0;padding:0;box-sizing:border-box}
html,body{width:737px;height:1200px;overflow:hidden;background:var(--paper)}
body{position:relative;font-family:'Jost',sans-serif;color:var(--ink)}
.header{position:absolute;left:0;top:0;width:737px;height:54px}
.brand{position:absolute;left:54px;top:14px;display:flex;align-items:center;gap:5px;color:var(--brand);font-weight:600;font-size:19px;letter-spacing:.3px}
.brand-dot{width:12px;height:12px;border-radius:50%;background:var(--brand)}
.nav{position:absolute;top:22px;font-size:7.6px;letter-spacing:.7px;font-weight:400;color:var(--ink)}
.nav.active{color:var(--brand)}
.nav.active::after{content:"";position:absolute;left:0;top:12px;width:9px;height:1.2px;background:var(--brand)}
.socials{position:absolute;left:620px;top:23px;display:flex;gap:9px}
.socials span{width:9px;height:9px;border-radius:50%;background:var(--ink)}
.socials span.accent{background:var(--brand)}
.hero{position:absolute;left:0;top:54px;width:737px;height:94px}
.hero h1{position:absolute;left:0;width:737px;top:24px;text-align:center;color:#fff;font-weight:500;font-size:22px}
.card{position:absolute;width:199px;height:231px;background:#fff;box-shadow:0 1px 6px rgba(0,0,0,.07)}
.card .photo{width:199px;height:113px}
.date{position:absolute;left:16px;top:126px;width:30px;text-align:center}
.date b{display:block;color:var(--brand);font-weight:600;font-size:18px;line-height:18px}
.date small{display:block;font-size:6.6px;font-weight:500;color:#555;margin-top:2px}
.divider{position:absolute;left:48px;top:126px;width:.6px;height:29px;background:var(--line)}
.title{position:absolute;left:58px;top:128px;width:130px;font-size:10px;font-weight:500;line-height:11px}
.excerpt{position:absolute;left:58px;top:159px;width:132px;font-size:7.3px;font-weight:300;color:var(--muted);line-height:11px}
.more{position:absolute;left:58px;top:199px;width:65px;height:17px;border:.7px solid #bbb;border-radius:9px;font-size:6.2px;text-align:center;line-height:16px;letter-spacing:.2px}
.pager{position:absolute;top:950px;width:22px;height:22px;border-radius:50%;border:.7px solid var(--line);font-size:9px;text-align:center;line-height:21px;color:var(--hero)}
.pager.current{background:var(--brand);border-color:var(--brand);color:#fff}
.footer{position:absolute;left:0;top:1002px;width:737px;height:172px;background:var(--footer);color:var(--footer-text)}
.f-brand{position:absolute;left:54px;top:70px;color:var(--brand);font-weight:600;font-size:19px}
.f-mark{position:absolute;left:97px;top:44px;width:14px;height:14px;border-radius:50%;background:#fff}
.f-social{position:absolute;left:63px;top:109px;display:flex;gap:16px}
.f-social span{width:9px;height:9px;border-radius:50%;background:#fff}
.f-social span.accent{background:var(--brand)}
.f-head{position:absolute;top:36px;color:var(--brand);font-weight:500;font-size:11px}
.links{position:absolute;left:201px;top:62px;list-style:none;font-size:8.3px;line-height:16.2px;font-weight:300}
.links li:first-child{color:var(--brand);text-decoration:underline}
.contact{position:absolute;left:315px;font-size:8.3px;font-weight:300;display:flex;gap:10px;line-height:12px}
.contact svg{flex:none;margin-top:1px}
.map{position:absolute;left:491px;top:35px;width:192px;height:107px;border-radius:5px}
.copyright{position:absolute;left:0;top:1174px;width:737px;height:26px;background:var(--brand);color:#fff;font-size:7.6px;text-align:center;line-height:26px;font-weight:300}
</style>
</head>
<body>
<header class="header">
  <div class="brand"><span class="brand-dot"></span>PaceKite</div>
  <span class="nav" style="left:287px">HOME</span>
  <span class="nav" style="left:332px">ABOUT</span>
  <span class="nav" style="left:380px">PRODUCTS</span>
  <span class="nav" style="left:443px">REVIEWS</span>
  <span class="nav active" style="left:500px">BLOGS</span>
  <span class="nav" style="left:548px">CONTACT US</span>
  <div class="socials"><span></span><span></span><span class="accent"></span><span></span></div>
</header>

<section class="hero">
  <svg width="737" height="94" viewBox="0 0 737 94" aria-hidden="true">
    <defs><linearGradient id="heroFade" x1="0" y1="0" x2="1" y2="1">
      <stop offset="0" stop-color="#0a2a66"/><stop offset=".5" stop-color="#123a86"/><stop offset="1" stop-color="#0a2a66"/>
    </linearGradient></defs>
    <path d="M0 0H737V94Q368 64 0 94Z" fill="url(#heroFade)"/>
  </svg>
  <h1>Blogs</h1>
</section>

<main>
  <article class="card" style="left:54px;top:194px">
    <div class="photo" role="img" aria-label="Red, black and white high-top sneakers on a court" style="background:linear-gradient(135deg,#9fb3c6,#5a7894)"></div>
    <div class="date"><b>18</b><small>Jul, 21</small></div><div class="divider"></div>
    <h2 class="title">Lorem Ipsum is simply dummy text of the printing</h2>
    <p class="excerpt">Lorem Ipsum has been the industry's standard dummy text ever since the 1500s, when an unknown...</p>
    <span class="more">READ MORE</span>
  </article>
  <article class="card" style="left:269px;top:194px">
    <div class="photo" role="img" aria-label="White running shoes hanging by laces on blue" style="background:linear-gradient(135deg,#16c3ee,#0aa9d9)"></div>
    <div class="date"><b>15</b><small>Jul, 21</small></div><div class="divider"></div>
    <h2 class="title">Lorem Ipsum is simply dummy text of the printing</h2>
    <p class="excerpt">Lorem Ipsum has been the industry's standard dummy text ever since the 1500s, when an unknown...</p>
    <span class="more">READ MORE</span>
  </article>
  <article class="card" style="left:483px;top:194px">
    <div class="photo" role="img" aria-label="Blue suede high heels on yellow" style="background:linear-gradient(135deg,#f1f55a,#2f5bb8 55%,#eef258)"></div>
    <div class="date"><b>03</b><small>Jun, 21</small></div><div class="divider"></div>
    <h2 class="title">Lorem Ipsum is simply dummy text of the printing</h2>
    <p class="excerpt">Lorem Ipsum has been the industry's standard dummy text ever since the 1500s, when an unknown...</p>
    <span class="more">READ MORE</span>
  </article>

  <article class="card" style="left:54px;top:440px">
    <div class="photo" role="img" aria-label="Black and white basketball sneakers on dark background" style="background:linear-gradient(135deg,#1a1a1c,#3a3a42 60%,#1a1a1c)"></div>
    <div class="date"><b>18</b><small>Jul, 21</small></div><div class="divider"></div>
    <h2 class="title">Lorem Ipsum is simply dummy text of the printing</h2>
    <p class="excerpt">Lorem Ipsum has been the industry's standard dummy text ever since the 1500s, when an unknown...</p>
    <span class="more">READ MORE</span>
  </article>
  <article class="card" style="left:269px;top:440px">
    <div class="photo" role="img" aria-label="Black strap shoe on grey backdrop" style="background:linear-gradient(135deg,#8d8b90,#5f5d63)"></div>
    <div class="date"><b>15</b><small>Jul, 21</small></div><div class="divider"></div>
    <h2 class="title">Lorem Ipsum is simply dummy text of the printing</h2>
    <p class="excerpt">Lorem Ipsum has been the industry's standard dummy text ever since the 1500s, when an unknown...</p>
    <span class="more">READ MORE</span>
  </article>
  <article class="card" style="left:483px;top:440px">
    <div class="photo" role="img" aria-label="Black and tan leather brogues" style="background:linear-gradient(135deg,#2a1409,#7a3a15 60%,#b5631f)"></div>
    <div class="date"><b>03</b><small>Jun, 21</small></div><div class="divider"></div>
    <h2 class="title">Lorem Ipsum is simply dummy text of the printing</h2>
    <p class="excerpt">Lorem Ipsum has been the industry's standard dummy text ever since the 1500s, when an unknown...</p>
    <span class="more">READ MORE</span>
  </article>

  <article class="card" style="left:54px;top:686px">
    <div class="photo" role="img" aria-label="Blue canvas sneakers and earphones on wood" style="background:linear-gradient(135deg,#4b4a48,#33407a 65%,#5a5954)"></div>
    <div class="date"><b>18</b><small>Jul, 21</small></div><div class="divider"></div>
    <h2 class="title">Lorem Ipsum is simply dummy text of the printing</h2>
    <p class="excerpt">Lorem Ipsum has been the industry's standard dummy text ever since the 1500s, when an unknown...</p>
    <span class="more">READ MORE</span>
  </article>
  <article class="card" style="left:269px;top:686px">
    <div class="photo" role="img" aria-label="Red and white high-tops on concrete steps" style="background:linear-gradient(135deg,#5f6a76,#7a2230 55%,#6e7782)"></div>
    <div class="date"><b>15</b><small>Jul, 21</small></div><div class="divider"></div>
    <h2 class="title">Lorem Ipsum is simply dummy text of the printing</h2>
    <p class="excerpt">Lorem Ipsum has been the industry's standard dummy text ever since the 1500s, when an unknown...</p>
    <span class="more">READ MORE</span>
  </article>
  <article class="card" style="left:483px;top:686px">
    <div class="photo" role="img" aria-label="Grey sneakers with red laces on asphalt" style="background:linear-gradient(135deg,#2b2b2b,#8a8a8a 45%,#c23a22 70%,#2b2b2b)"></div>
    <div class="date"><b>03</b><small>Jun, 21</small></div><div class="divider"></div>
    <h2 class="title">Lorem Ipsum is simply dummy text of the printing</h2>
    <p class="excerpt">Lorem Ipsum has been the industry's standard dummy text ever since the 1500s, when an unknown...</p>
    <span class="more">READ MORE</span>
  </article>

  <nav aria-label="Pagination">
    <span class="pager current" style="left:303px">1</span>
    <span class="pager" style="left:330px">2</span>
    <span class="pager" style="left:357px">3</span>
    <span class="pager" style="left:384px">•••</span>
    <span class="pager" style="left:411px"><svg width="8" height="8" viewBox="0 0 8 8" style="margin-top:7px"><path d="M2.5 1L5.5 4L2.5 7" stroke="#0c2f72" stroke-width="1.2" fill="none"/></svg></span>
  </nav>
</main>

<footer class="footer">
  <span class="f-mark"></span>
  <div class="f-brand">PaceKite</div>
  <div class="f-social"><span></span><span></span><span class="accent"></span><span></span></div>

  <h3 class="f-head" style="left:201px">Quick Link</h3>
  <ul class="links">
    <li>Home</li><li>About Us</li><li>Products</li><li>Testimonials</li><li>Blogs</li><li>Contact Us</li>
  </ul>

  <h3 class="f-head" style="left:315px">Conatct info</h3>
  <div class="contact" style="top:63px">
    <svg width="9" height="12" viewBox="0 0 9 12"><path d="M4.5 0A4.5 4.5 0 0 0 0 4.5C0 8 4.5 12 4.5 12S9 8 9 4.5A4.5 4.5 0 0 0 4.5 0Z" fill="#1d56b6"/><circle cx="4.5" cy="4.5" r="1.7" fill="#0b0b0b"/></svg>
    <span>lorem ipsum, 128 Harbor Lane<br>Millbrook, OR &nbsp;97201</span>
  </div>
  <div class="contact" style="top:111px">
    <svg width="9" height="9" viewBox="0 0 9 9"><path d="M1.8 0L3.6 2.2L2.6 3.4Q3.6 5.4 5.6 6.4L6.8 5.4L9 7.2L7.8 9Q1 8 0 1.2Z" fill="#1d56b6"/></svg>
    <span>503.555.0142</span>
  </div>
  <div class="contact" style="top:135px">
    <svg width="10" height="8" viewBox="0 0 10 8"><rect width="10" height="8" fill="#1d56b6"/><path d="M0 0L5 4.5L10 0" stroke="#0b0b0b" stroke-width="1" fill="none"/></svg>
    <span>info@pacekite.com</span>
  </div>

  <div class="map" role="img" aria-label="Street map showing the store location" style="background:linear-gradient(135deg,#f1f1ee,#e4e7ea 60%,#eef0e6)"></div>
</footer>

<div class="copyright">Copyright © 2021 PaceKite. All Rights Reserved</div>
</body>
</html>
```